VIP Card Design Project

uZorvo is a premium sneaker store selling brand name sneakers like Volta, Rexa, Kembro and etc. ( www.uzorvoshop.com ) We need to design a VIP card to promote one of our discount program called "Uzorvo VIP Band 17", which offers 24% discount off all full-priced items. The idea is because we have a "Peakline Gym center" (peaklinegym.com) next door and we are trying to design a discount program for people going to the fitness center.
The design is for the front of the card. The back will be black and white with benefits information and member information.
The front design need to include our logo, "VIP", "Band 17" and our web address "Uzorvo.com" and Chatterly and quibbr logo.
It will be a plastic card in the size of 3.375x2.125 (bleed size 3.5x2.25)

```html
<!DOCTYPE html>
<html lang="en">
<head>
<meta charset="utf-8">
<title>Uzorvo VIP Band 17 – Card Front and Back</title>
<link rel="stylesheet" href="https://fonts.googleapis.com/css2?family=Arimo:ital,wght@0,400;0,700;1,700&family=Russo+One&display=swap">
<style>
  :root {
    --page: #e9e6e1;
    --card-black: #050505;
    --brand-green: #3fb549;
    --web-orange: #f29a1e;
    --title-red: #d71920;
    --band-yellow: #f4ea3a;
    --pale-yellow: #fff4a8;
    --text-white: #f2f2f2;
    --ink: #111;
    --shadow: rgba(0,0,0,.35);
  }
  * { box-sizing: border-box; margin: 0; padding: 0; }
  html, body { width: 1200px; height: 665px; overflow: hidden; }
  body {
    background: var(--page);
    font-family: "Arimo", Arial, sans-serif;
    position: relative;
  }
  .card {
    position: absolute;
    top: 167px;
    width: 540px;
    height: 330px;
    background: var(--card-black);
    border-radius: 6px;
    box-shadow: 0 6px 18px var(--shadow);
    overflow: hidden;
  }
  .card--front { left: 40px; }
  .card--back { left: 620px; }

  /* front */
  .front-sheen {
    position: absolute; inset: 0;
    background: radial-gradient(ellipse 70% 55% at 55% 35%, rgba(120,120,120,.35), rgba(0,0,0,0) 70%);
  }
  .brand-logo {
    position: absolute; left: 30px; top: 38px;
    font-weight: 700; font-size: 86px; line-height: 1;
    color: var(--brand-green); letter-spacing: 1px;
  }
  .social {
    position: absolute; right: 22px; top: 22px;
    display: flex; flex-direction: column; align-items: flex-end; gap: 14px;
  }
  .social__item {
    display: flex; align-items: center; gap: 6px;
    font-weight: 700; font-size: 13px; color: var(--text-white);
  }
  .social__item::after {
    content: ""; width: 30px; height: 30px; border-radius: 5px;
    background: #2e8fd6;
  }
  .social__item--chatterly::after { background: #3b5fa8; }
  .web-address {
    position: absolute; left: 112px; top: 140px;
    font-weight: 700; font-size: 16px; color: var(--web-orange); letter-spacing: .5px;
  }
  .club-title {
    position: absolute; left: 118px; top: 158px;
    font-family: "Russo One", Arial, sans-serif;
    font-size: 30px; line-height: 36px; color: var(--title-red); letter-spacing: .5px;
    z-index: 2;
  }
  .product {
    position: absolute; top: 206px; height: 90px; border-radius: 4px;
  }
  .product--one { left: 40px; width: 140px; background: linear-gradient(135deg, #b9a05a, #c8412d 55%, #3a3a3a); }
  .product--two { left: 188px; width: 148px; background: linear-gradient(135deg, #c45a1e, #e9e6dc 50%, #2d5fb0); }
  .product--three { left: 344px; width: 136px; top: 196px; height: 80px; background: linear-gradient(135deg, #8a7f78, #f1efef 50%, #c8322a); }
  .offer-band {
    position: absolute; left: 80px; top: 296px; width: 420px; height: 20px;
    background: var(--band-yellow); border-radius: 0 10px 10px 0;
    font-weight: 700; font-size: 13px; color: var(--ink);
    letter-spacing: 1.2px; line-height: 20px; padding-left: 58px;
  }
  .offer-burst { position: absolute; left: 14px; top: 270px; width: 72px; height: 60px; }

  /* back */
  .benefits-title {
    position: absolute; left: 0; right: 0; top: 20px; text-align: center;
    font-weight: 700; font-size: 24px; line-height: 30px; color: var(--brand-green);
  }
  .benefits {
    position: absolute; left: 26px; right: 20px; top: 68px;
    color: var(--text-white); font-size: 11.5px; line-height: 1.25;
  }
  .benefits__intro { margin-bottom: 6px; }
  .benefits__list { list-style: none; }
  .benefits__list li { display: flex; gap: 6px; margin-bottom: 6px; padding-left: 12px; }
  .benefits__letter { flex: 0 0 14px; }
  .member-band {
    position: absolute; left: 0; right: 0; bottom: 0; height: 58px;
    background: linear-gradient(180deg, var(--pale-yellow), #f7e98a);
    font-size: 13px; color: var(--ink);
  }
  .member-field {
    position: absolute; display: flex; align-items: flex-end; gap: 6px;
  }
  .member-field__line { border-bottom: 1px solid #777; height: 1px; }
  .member-field--name { left: 44px; bottom: 10px; }
  .member-field--name .member-field__line { width: 300px; }
  .member-field--id { right: 24px; bottom: 34px; }
  .member-field--id .member-field__line { width: 130px; }
</style>
</head>
<body>

<section class="card card--front" aria-label="Card front">
  <div class="front-sheen" role="img" aria-label="Soft grey wave decoration"></div>
  <div class="brand-logo">uZorvo</div>
  <div class="social">
    <span class="social__item social__item--quibbr">quibbr</span>
    <span class="social__item social__item--chatterly">Chatterly</span>
  </div>
  <div class="web-address">www.Uzorvo.com</div>
  <div class="product product--one" role="img" aria-label="Photo of a red and grey Volta running sneaker"></div>
  <div class="product product--two" role="img" aria-label="Photo of a white, blue and orange basketball sneaker"></div>
  <div class="product product--three" role="img" aria-label="Photo of a white and red basketball sneaker"></div>
  <div class="club-title">Uzorvo VIP Band 17</div>
  <div class="offer-band">DISCOUNT OFF ALL FULL-PRICED ITEMS.</div>
  <svg class="offer-burst" viewBox="0 0 72 60" aria-label="24% badge">
    <polygon fill="#f4ea3a" points="36,0 42,12 56,5 53,19 70,18 59,29 72,38 56,41 61,56 46,49 38,60 31,49 16,56 20,42 2,40 14,30 1,19 18,19 15,5 30,12"/>
    <text x="36" y="36" text-anchor="middle" font-family="Arimo, Arial, sans-serif" font-weight="700" font-size="16" fill="#d71920">24%</text>
  </svg>
</section>

<section class="card card--back" aria-label="Card back">
  <h2 class="benefits-title">-: Benefits :-</h2>
  <div class="benefits">
    <p class="benefits__intro">The UZORVO Member Program entitles Members to the following benefits:</p>
    <ol class="benefits__list">
      <li><span class="benefits__letter">a.</span><span>20% OFF your entire first purchase after you sign up (Limited Time Offer). Certain items are excluded from this offer. Please see stores for details.</span></li>
      <li><span class="benefits__letter">b.</span><span>10% OFF every purchase while being a member. Certain items are excluded from this offer. Please see stores for details.</span></li>
      <li><span class="benefits__letter">c.</span><span>Additional 10% OFF and FREE SHIPPING when an item is out of stock in store but can be shipped to you from another location.</span></li>
      <li><span class="benefits__letter">d.</span><span>Eligible to purchase exclusive items offered to members only. Purchasing of exclusive items is limited to 1 item per member per 30 days. Please see stores for details.</span></li>
    </ol>
  </div>
  <div class="member-band">
    <div class="member-field member-field--id"><span>Member ID :</span><span class="member-field__line"></span></div>
    <div class="member-field member-field--name"><span>Member Name :</span><span class="member-field__line"></span></div>
  </div>
</section>

</body>
</html>
```